QuillVane needs a dashboard page designed

Redesign the dashboard shown in the provided images.

There are two images:
- dashboard.png
- dashboard-expanded.png

NOTE: The vocabulary navigation on the left will be a very long list of words 100s, so keep that in mind when you're designing both the vocab navigation and the expanded vocab popup.

In the dashboard.png picture, there needs to be a progress chart showing the word progress like the following: review 1(show it as completed) -> review 2(show the user they are here) -> review 3(unvisited) -> review 4(unvisited)

The do-not-design-this-page.png image is for your reference only. It is not to be designed. Use it to understand the overall look and feel of the website to help you create the best dashboard page possible.
Updates

Need extra days to review

Industry/Entity Type

Education English learning

Number of Pages Required

1 page

Requirements
Must have
• The main navigation and main header cannot change between pages. See the do-not-design page for the main navigateion and header.
Should not have
• Do not add a person profile. We will not have images of our users. Keep the icons in the main navigation as they are.

```html
<!DOCTYPE html>
<html lang="en">
<head>
<meta charset="utf-8">
<title>QuillVane Dashboard</title>
<link href="https://fonts.googleapis.com/css2?family=Figtree:wght@300;400;500;600;700&display=swap" rel="stylesheet">
<style>
:root{
  --chrome:#272727;
  --chrome-text:#b4b4b4;
  --page:#ffffff;
  --panel:#d8edf4;
  --panel-line:#c4dce5;
  --ink:#2b2b2b;
  --muted:#6f7478;
  --blue:#1f86c4;
  --orange:#f0a21f;
  --gray-step:#bfc4c6;
  --scrim:rgba(0,0,0,.27);
  --modal:#262626;
  --chip:#cde7f6;
  --chip-active:#3d8ef0;
  --white:#ffffff;
}
*{box-sizing:border-box;margin:0;padding:0}
html,body{width:1200px;height:836px;overflow:hidden;background:var(--chrome)}
body{font-family:"Figtree",sans-serif;color:var(--ink)}
.stage{position:relative;width:1400px;height:975px;transform:scale(.8572);transform-origin:0 0;background:var(--page);overflow:hidden}
.abs{position:absolute}

.top-bar{left:0;top:0;width:1400px;height:54px;background:var(--chrome)}
.brand{left:94px;top:10px;font-size:24px;font-weight:700;color:var(--chrome-text)}
.top-icons{right:44px;top:16px;display:flex;gap:22px}
.top-icons svg{width:18px;height:18px;fill:var(--chrome-text)}

.side-nav{left:0;top:54px;width:93px;height:921px;background:var(--chrome)}
.nav-item{position:absolute;left:0;width:93px;text-align:center;font-size:11px;color:var(--chrome-text)}
.nav-item svg{display:block;margin:0 auto 3px;width:18px;height:18px;fill:var(--chrome-text)}

.vocab-nav{left:127px;top:72px;width:240px;height:806px;background:var(--panel);border-radius:8px;overflow:hidden}
.vocab-filter{position:absolute;left:16px;top:14px;width:74px;height:32px;border:1.5px solid var(--blue);border-radius:16px;font-size:15px;color:#4a6a80;padding:6px 0 0 10px}
.vocab-expand{position:absolute;left:148px;top:22px;font-size:12px;color:#4a4a4a}
.group-title{position:absolute;left:8px;font-size:12.5px;color:#333;display:flex;align-items:center;gap:8px;width:224px;height:26px;border-bottom:1px solid var(--panel-line)}
.group-title .help{margin-left:auto;margin-right:30px}
.word{position:absolute;left:0;width:240px;padding-left:31px;font-size:12.5px;color:var(--muted);height:24px;line-height:24px;border-bottom:1px solid var(--panel-line)}

.stepper{left:460px;top:88px;width:800px;height:80px}
.step-label{position:absolute;top:53px;font-size:15px;color:#333;transform:translateX(-50%)}

.word-card{left:374px;top:183px;width:986px;height:162px;background:var(--panel);border-radius:10px}
.word-title{position:absolute;left:58px;top:20px;font-size:24px;font-weight:600;display:flex;align-items:center}
.word-star{position:absolute;left:22px;top:23px;width:24px;height:24px;fill:var(--orange)}
.review-btn{position:absolute;left:641px;top:21px;width:317px;height:38px;background:var(--orange);border-radius:19px;color:#3a2a0a;font-size:15px;text-align:center;line-height:38px}
.word-desc{position:absolute;left:28px;top:75px;width:930px;font-size:14.5px;line-height:17px;color:#333}

.chart-card{left:374px;top:355px;width:986px;height:402px;background:var(--panel);border-radius:10px}
.axis-title{position:absolute;left:0;width:1076px;top:368px;text-align:center;font-size:15px;font-weight:600}

.analysis{left:393px;top:767px;width:930px}
.analysis h2{font-size:24px;font-weight:600;margin-bottom:6px}
.analysis p{font-size:14.5px;line-height:17px;color:#333}
.footer{left:0;top:927px;width:1400px;text-align:center;font-size:15px;color:#444}

.scrim{left:93px;top:54px;width:1307px;height:921px;background:var(--scrim)}

.vocab-modal{left:220px;top:311px;width:960px;height:380px;background:var(--modal);border-radius:22px;color:var(--white)}
.modal-select{position:absolute;left:72px;top:38px;width:98px;height:34px;border:1.5px solid var(--white);border-radius:7px;font-size:13px;padding:8px 0 0 14px}
.modal-select svg{position:absolute;right:10px;top:12px;width:10px;height:10px;stroke:var(--white);fill:none;stroke-width:2}
.modal-close{position:absolute;right:22px;top:26px;font-size:13px}
.modal-group{position:absolute;left:71px;font-size:19px;font-weight:400}
.chip-row{position:absolute;left:71px;display:flex;gap:6px}
.chip{background:var(--chip);color:#222;border-radius:12px;height:24px;line-height:24px;padding:0 12px;font-size:13px}
.chip.active{background:var(--chip-active);color:var(--white);font-size:15px;padding:0 19px}
</style>
</head>
<body>
<div class="stage">

  <header class="abs top-bar"></header>
  <div class="abs brand">QuillVane</div>
  <div class="abs top-icons">
    <svg viewBox="0 0 20 20"><path d="M10 6.5a3.5 3.5 0 1 0 0 7 3.5 3.5 0 0 0 0-7zm7 2.3-1.8-.4-.5-1.2 1-1.6-1.6-1.6-1.6 1-1.2-.5L11.2 2H8.8l-.4 1.8-1.2.5-1.6-1-1.6 1.6 1 1.6-.5 1.2L2.7 8.8v2.4l1.8.4.5 1.2-1 1.6 1.6 1.6 1.6-1 1.2.5.4 1.8h2.4l.4-1.8 1.2-.5 1.6 1 1.6-1.6-1-1.6.5-1.2 1.8-.4z"/></svg>
    <svg viewBox="0 0 20 20"><path d="M10 3C5.6 3 2 5.8 2 9.3c0 1.8 1 3.5 2.6 4.6L4 17l3.5-2c.8.2 1.6.3 2.5.3 4.4 0 8-2.8 8-6.3S14.4 3 10 3zM6.5 10.3a1 1 0 1 1 0-2 1 1 0 0 1 0 2zm3.5 0a1 1 0 1 1 0-2 1 1 0 0 1 0 2zm3.5 0a1 1 0 1 1 0-2 1 1 0 0 1 0 2z"/></svg>
    <svg viewBox="0 0 20 20"><circle cx="10" cy="6" r="4"/><path d="M2.5 18c0-4 3.4-6.5 7.5-6.5s7.5 2.5 7.5 6.5z"/></svg>
  </div>

  <nav class="abs side-nav">
    <div class="nav-item" style="top:22px"><svg viewBox="0 0 20 20"><path d="M10 2 1 10h3v8h4.5v-5h3v5H16v-8h3z"/></svg>Quill Tutor</div>
    <div class="nav-item" style="top:85px"><svg viewBox="0 0 20 20"><path d="M2 8h5v10H2zm5.5-3h5v13h-5zM13 6h5v12h-5z"/><circle cx="10" cy="3" r="2"/></svg>Daily English</div>
    <div class="nav-item" style="top:150px"><svg viewBox="0 0 20 20"><path d="M4 2h12v16h-4.5v-4h-3v4H4zm3 3v2h2V5zm4 0v2h2V5zM7 9v2h2V9zm4 0v2h2V9z"/></svg>Business</div>
  </nav>

  <aside class="abs vocab-nav">
    <div class="vocab-filter">ALL
      <svg style="position:absolute;right:9px;top:11px;width:10px;height:10px;fill:none;stroke:#4a6a80;stroke-width:2" viewBox="0 0 10 10"><path d="M1 3l4 4 4-4"/></svg>
    </div>
    <div class="vocab-expand">EXPAND &#x26F6;</div>

    <div class="group-title" style="top:78px">
      <svg width="12" height="12" viewBox="0 0 12 12"><circle cx="6" cy="6" r="6" fill="#333"/><path d="M6 3v3l2 1" stroke="#d8edf4" stroke-width="1.3" fill="none"/></svg>
      SHORT - TERM MEMORY
      <svg class="help" width="12" height="12" viewBox="0 0 12 12"><circle cx="6" cy="6" r="6" fill="#333"/><text x="6" y="9" font-size="8" text-anchor="middle" fill="#d8edf4">?</text></svg>
    </div>
    <div class="word" style="top:109px">Grab</div>

    <div class="group-title" style="top:159px">
      <svg width="12" height="12" viewBox="0 0 12 12"><rect x="2" y="2" width="8" height="8" rx="2" fill="#333"/><path d="M0 4h2M0 8h2M10 4h2M10 8h2M4 0v2M8 0v2M4 10v2M8 10v2" stroke="#333"/></svg>
      WORKING MEMORY
      <svg class="help" width="12" height="12" viewBox="0 0 12 12"><circle cx="6" cy="6" r="6" fill="#333"/><text x="6" y="9" font-size="8" text-anchor="middle" fill="#d8edf4">?</text></svg>
    </div>
    <div class="word" style="top:192px">Cool Down</div>
    <div class="word" style="top:216px">Crave</div>
    <div class="word" style="top:240px">Go For</div>
    <div class="word" style="top:264px">Go-To</div>
    <div class="word" style="top:288px">In The Mood For</div>
    <div class="word" style="top:312px">Sip</div>
    <div class="word" style="top:336px">Soothing</div>
    <div class="word" style="top:360px">Stick With</div>
    <div class="word" style="top:384px">Throw in / Throw On</div>

    <div class="group-title" style="top:426px">
      <svg width="12" height="12" viewBox="0 0 12 12"><rect x="1" y="5" width="10" height="7" rx="1" fill="#333"/><path d="M3.5 5V3.5a2.5 2.5 0 0 1 5 0V5" stroke="#333" stroke-width="1.4" fill="none"/></svg>
      LONG - TERM MEMORY
    </div>
    <div class="word" style="top:459px">Give It A Try</div>
  </aside>

  <div class="abs stepper">
    <svg width="800" height="50" viewBox="0 0 800 50">
      <line x1="71" y1="25" x2="295" y2="25" stroke="var(--blue)" stroke-width="5"/>
      <line x1="295" y1="25" x2="744" y2="25" stroke="var(--gray-step)" stroke-width="5"/>
      <circle cx="71" cy="25" r="24" fill="var(--blue)"/>
      <circle cx="295" cy="25" r="24" fill="var(--orange)"/>
      <circle cx="520" cy="25" r="24" fill="var(--gray-step)"/>
      <circle cx="744" cy="25" r="24" fill="var(--gray-step)"/>
      <g font-family="Figtree, sans-serif" font-size="18" font-weight="700" text-anchor="middle" fill="#fff">
        <text x="71" y="31">01</text><text x="295" y="31">02</text><text x="520" y="31">03</text><text x="744" y="31">04</text>
      </g>
    </svg>
    <span class="step-label" style="left:71px">Review 1</span>
    <span class="step-label" style="left:295px">Review 2</span>
    <span class="step-label" style="left:520px">Review 3</span>
    <span class="step-label" style="left:744px">Review 4</span>
  </div>

  <section class="abs word-card">
    <svg class="word-star" viewBox="0 0 24 24"><path d="M12 1.5l3.2 6.8 7.3.9-5.4 5 1.4 7.3L12 17.9l-6.5 3.6 1.4-7.3-5.4-5 7.3-.9z"/></svg>
    <div class="word-title">Grab</div>
    <div class="review-btn">Start Vocabulary Review Exercise 3</div>
    <p class="word-desc">The word "grab" is most commonly used as averb, meaning to take something quickly or suddenly. Imagine you're running late for school. You don't have time for breakfast, so you quickly grab an apple from the kitchen and rush out the door. As you reach the bus stop, your friend waves and says, "Hey! Let's grab a coffee after class." Later, when you sit down, your phone starts ringing. You grab it before it stops.</p>
  </section>

  <section class="abs chart-card">
    <svg class="abs" style="left:0;top:0" width="986" height="360" viewBox="0 0 986 360">
      <rect x="28" y="40" width="938" height="67" fill="#cde0e8"/>
      <rect x="28" y="115" width="938" height="148" fill="#bfe2df"/>
      <rect x="28" y="263" width="938" height="32" fill="#f4e6c4"/>
      <line x1="28" y1="325" x2="966" y2="325" stroke="#333" stroke-width="1"/>
      <line x1="28" y1="325" x2="28" y2="352" stroke="#333"/>
      <g stroke="#333">
        <line x1="810" y1="325" x2="810" y2="333"/><line x1="855" y1="325" x2="855" y2="333"/>
        <line x1="900" y1="325" x2="900" y2="333"/><line x1="948" y1="325" x2="948" y2="333"/>
      </g>
      <g font-family="Figtree, sans-serif" font-size="13" fill="#444">
        <text x="54" y="348">18 May</text><text x="110" y="348">12:00</text>
        <text x="157" y="348">19 May</text><text x="209" y="348">12:00</text>
        <text x="248" y="348">20 May</text><text x="308" y="348">12:00</text>
        <text x="355" y="348">21 May</text><text x="407" y="348">12:00</text>
        <text x="452" y="348">22 May</text><text x="505" y="348">12:00</text>
        <text x="551" y="348">23 May</text><text x="608" y="348">12:00</text>
        <text x="654" y="348">24 May</text><text x="707" y="348">12:00</text>
        <text x="745" y="348">25 May</text><text x="795" y="348">12:00</text>
        <text x="832" y="348">26 May</text><text x="885" y="348">12:00</text>
        <text x="924" y="348">27 May</text>
      </g>
    </svg>
    <div class="axis-title">Date Range</div>
  </section>

  <section class="abs analysis">
    <h2>QuillVane Tutor Learning Analysis</h2>
    <p>Lorem ipsum dolor sit amet, consectetur adipiscing elit. Nam rutrum commodo enim id bibendum. Nunc dignissim risus erat, nec finibus nunc dictum eu. Aliquam sit amet euismod metus, quis malesuada erat. Sed at felis quis nulla feugiat cursus at at dolor. Maecenas pretium aliquet dapibus. Fusce et eleifend massa. Sed convallis ex mi, at lobortis ligula congue vel. Pellentesque pharetra molestie leo, sed vehicula felis commodo molestie.</p>
  </section>

  <footer class="abs footer">© 2025 | www.quillvane.com</footer>

  <div class="abs scrim"></div>

  <div class="abs vocab-modal" role="dialog" aria-label="All vocabulary">
    <div class="modal-select">All <svg viewBox="0 0 10 10"><path d="M1 3l4 4 4-4"/></svg></div>
    <div class="modal-close">Close &nbsp;X</div>

    <div class="modal-group" style="top:106px">Short Term Memory</div>
    <div class="chip-row" style="top:138px;left:70px"><span class="chip active">Grab</span></div>

    <div class="modal-group" style="top:182px;left:73px">Working Memory</div>
    <div class="chip-row" style="top:218px">
      <span class="chip">Cool Down</span><span class="chip">Crave</span><span class="chip">Go For</span>
      <span class="chip">Go-To</span><span class="chip">In The Mood For</span><span class="chip">Sip</span>
      <span class="chip">Soothing</span><span class="chip">Stick With</span><span class="chip">Throw in / Throw On</span>
    </div>

    <div class="modal-group" style="top:263px;left:73px">Long Term Memory</div>
    <div class="chip-row" style="top:296px"><span class="chip">Give it a Try</span></div>
  </div>

</div>
</body>
</html>
```